NEW Modern Sleek Business Card for VR Language Startup

Our startup is using VR to lead the next wave of world language education. We need a two-sided business card that introduces the larger organization (Brightloom Language Inc) and our contact info on one side and shows the product, Glimwoorld, on the other side.

Side 1 (contact info)= Brightloom Logo and Contact info (name, title, phone, email)

Side 2 (product)= Glimworld logo, text, and website
Text= Culturally Immersive Language Learning Games
Website= www.glimworld-play.com

Target Market(s)

Education, Technology

Contact Information for Business Card

Contact info will be updated upon approval of the design. For now, put this as a placeholder.

Perry Dunmore
Founder & CEO
pdunmore@quillpost-mail.net
(555)-014-2286

Font styles to use
Other font styles liked:
• Gibson and Century Gothic are the brand fonts

Requirements
Nice to have
• I would love to see cohesion between the design and colors of the two logos. I have attached a few business card designs that I like, so you can get a feel for my preferred style.

```html
<!DOCTYPE html>
<html lang="en">
<head>
<meta charset="utf-8">
<title>Brightloom Language – Business Card</title>
<link rel="stylesheet" href="https://fonts.googleapis.com/css2?family=Lato:wght@400;700&display=swap">
<style>
  :root {
    --page-bg: #d9d9db;
    --card-front: #f7f8f8;
    --card-back: #fbf6f6;
    --ink: #2b2b2b;
    --ink-soft: #555555;
    --accent-blue: #1fa3f0;
    --accent-violet: #6a5cf0;
    --accent-orange: #f26a3d;
    --divider: #c9c9c9;
  }
  * { box-sizing: border-box; margin: 0; padding: 0; }
  html, body {
    width: 1200px; height: 782px; overflow: hidden;
    background: var(--page-bg);
    font-family: "Lato", sans-serif;
    color: var(--ink);
  }
  .sheet {
    width: 1200px; height: 782px;
    display: flex; flex-direction: column;
    align-items: center; justify-content: center; gap: 32px;
  }
  .card {
    width: 640px; height: 350px;
    box-shadow: 0 6px 18px rgba(0,0,0,0.18);
    position: relative;
  }

  /* Product side */
  .card--product {
    background: var(--card-front);
    display: flex; flex-direction: column;
    align-items: center; justify-content: center;
  }
  .product-mark {
    display: flex; align-items: center; gap: 14px;
    margin-bottom: 22px;
  }
  .product-mark__dot {
    width: 46px; height: 46px; border-radius: 50%;
    background: var(--accent-blue);
  }
  .product-mark__name {
    font-size: 50px; font-weight: 400; color: var(--ink-soft);
    letter-spacing: 0.5px;
  }
  .product-tagline {
    font-size: 15px; font-weight: 400; letter-spacing: 0.6px;
    text-transform: uppercase; color: var(--ink);
    margin-bottom: 14px;
  }
  .product-url {
    font-size: 17px; color: var(--accent-blue);
  }

  /* Contact side */
  .card--contact {
    background: var(--card-back);
    display: flex; align-items: center;
  }
  .company-mark {
    width: 300px;
    display: flex; align-items: center; justify-content: center; gap: 12px;
  }
  .company-mark__dot {
    width: 34px; height: 34px; border-radius: 50%;
    background: var(--accent-orange);
  }
  .company-mark__name {
    font-size: 26px; font-weight: 700; color: var(--ink);
    letter-spacing: 1.5px;
  }
  .divider {
    width: 1px; height: 110px; background: var(--divider);
  }
  .contact {
    padding-left: 36px;
  }
  .contact__name {
    font-size: 22px; font-weight: 700; text-transform: uppercase;
    color: var(--accent-violet); letter-spacing: 0.5px;
  }
  .contact__title {
    font-size: 15px; color: var(--ink); margin-bottom: 20px;
  }
  .contact__line {
    display: flex; align-items: center; gap: 8px;
    font-size: 15px; color: var(--ink); margin-bottom: 6px;
  }
  .contact__icon { width: 15px; height: 15px; flex: none; }
</style>
</head>
<body>
<main class="sheet">
  <section class="card card--product" aria-label="Product side">
    <div class="product-mark">
      <span class="product-mark__dot" aria-hidden="true"></span>
      <span class="product-mark__name">Glimworld</span>
    </div>
    <p class="product-tagline">Culturally Immersive Language Learning Games</p>
    <p class="product-url">www.glimworld-play.com</p>
  </section>

  <section class="card card--contact" aria-label="Contact side">
    <div class="company-mark">
      <span class="company-mark__dot" aria-hidden="true"></span>
      <span class="company-mark__name">Brightloom Language</span>
    </div>
    <div class="divider" aria-hidden="true"></div>
    <div class="contact">
      <p class="contact__name">Perry Dunmore</p>
      <p class="contact__title">Founder &amp; CEO</p>
      <p class="contact__line">
        <svg class="contact__icon" viewBox="0 0 16 16" aria-hidden="true">
          <path fill="var(--accent-orange)" d="M3.6 1.5l2.3 2.4-1.3 1.9c.9 2 2.5 3.6 4.6 4.6l1.9-1.3 2.4 2.3-1.3 2.4C6.6 13.5 2.5 9.4 1.2 2.8z"/>
        </svg>
        (555)-014-2286
      </p>
      <p class="contact__line">
        <svg class="contact__icon" viewBox="0 0 16 16" aria-hidden="true">
          <rect x="1" y="3" width="14" height="10" rx="1" fill="var(--accent-violet)"/>
          <path d="M1.5 3.8L8 9l6.5-5.2" fill="none" stroke="#ffffff" stroke-width="1.3"/>
        </svg>
        pdunmore@quillpost-mail.net
      </p>
    </div>
  </section>
</main>
</body>
</html>
```